Corporate Design für Vermittlung von wertigen Immobilien
Zielgruppe
Vermittlung von wertigen Immobilien.
Zielgruppe sind Verkäufer von hochwertigen Gebäuden und Käufer, die ordentliche (wertige) Immobilien suchen.
Eventuell auch im Bereich Vermietung. Mein Fokus wird eher auf den Kaufobjekten liegen.
Aufgabenstellung
Liebe Designer, für meinen neuen Geschäftszweig (Makler) benötige ich Visitenkarten und Briefpapier. Des weiteren möchte ich gerne eine Präsentationsmappe , in der ich den Kunden Informationen zum Objekt (Exposé) und die Vertragsunterlagen (Maklervertrag) im Format DINA4 übergeben kann.
Das Design soll modern sein, aber auch Seriösität vermitteln. Durch meine über 10 jährige Tätigkeit als Sachverständiger für Immobilienbewertung hebe ich mich vom know how deutlich von den meisten Maklern ab.
Die Bürodaten (Anschrift usw.) können von meinem Auftritt des Sachverständigenbüros entnommen werden: www.taxoplan.net

```html
<!DOCTYPE html>
<html lang="de">
<head>
<meta charset="utf-8">
<title>Hauslumena – Geschäftsausstattung</title>
<link rel="stylesheet" href="https://fonts.googleapis.com/css2?family=Montserrat:wght@500;600&family=Open+Sans:wght@400;600&display=swap">
<style>
  :root{
    --navy:#22346d;
    --navy-deep:#1c2c5e;
    --paper:#ffffff;
    --paper-warm:#f7f8fa;
    --folder-light:#dfe4ec;
    --folder-shade:#cfd6e1;
    --backdrop:#c9ccd1;
    --ink:#2b2f3a;
    --ink-soft:#7a8090;
  }
  *{box-sizing:border-box;margin:0;padding:0}
  html,body{width:1200px;height:848px;overflow:hidden}
  body{background:var(--backdrop);font-family:"Open Sans",Arial,sans-serif;color:var(--ink);position:relative}
  .brand{font-family:"Montserrat",Arial,sans-serif;font-weight:600;color:var(--navy);letter-spacing:.08em;display:flex;align-items:center;gap:4px;white-space:nowrap}
  .brand .mark{width:6px;height:6px;background:currentColor;display:inline-block}
  .brand--light{color:var(--paper)}

  /* presentation folder */
  .folder{position:absolute;left:233px;top:193px;width:473px;height:327px}
  .folder__panel{position:absolute;top:0;height:100%;width:236px}
  .folder__panel--left{left:0;background:linear-gradient(180deg,var(--folder-light),var(--folder-shade))}
  .folder__panel--right{left:237px;background:var(--folder-light)}
  .folder__panel--left .brand{position:absolute;left:18px;top:28px;font-size:8px}
  .pocket{position:absolute;bottom:0;background:var(--navy)}
  .pocket--left{left:0;width:236px;height:115px;clip-path:polygon(0 0,88% 0,100% 22%,100% 100%,0 100%);background:linear-gradient(90deg,var(--navy-deep),var(--navy))}
  .pocket--right{left:237px;width:236px;height:72px;clip-path:polygon(0 30%,6% 0,100% 0,100% 100%,0 100%)}

  /* letterhead sheet */
  .sheet{position:absolute;background:var(--paper)}
  .sheet .brand{position:absolute;right:12px;top:16px;font-size:8px}
  .sheet__sender{position:absolute;left:18px;top:58px;font-size:3px;color:var(--ink-soft);white-space:nowrap}
  .sheet__sender b{color:var(--navy);font-weight:600}
  .sheet__address{position:absolute;left:18px;top:66px;font-size:4px;line-height:1.45}
  .sheet__footer{position:absolute;left:18px;right:12px;bottom:10px;display:flex;gap:10px;font-size:3px;line-height:1.5;color:var(--ink-soft)}
  .sheet__footer div{flex:1;border-left:1px solid var(--navy);padding-left:4px;white-space:nowrap}
  .sheet--in-folder{left:258px;top:10px;width:210px;height:317px}
  .sheet--single{left:745px;top:215px;width:215px;height:305px;box-shadow:0 0 0 1px #e6e8ec}

  /* envelope */
  .envelope{position:absolute;left:488px;top:555px;width:235px;height:116px;background:var(--paper-warm)}
  .envelope__flap{position:absolute;left:0;top:0;width:100%;height:24px;background:var(--navy);clip-path:polygon(0 0,100% 0,100% 75%,56% 75%,50% 100%,44% 75%,0 75%)}
  .envelope .brand{position:absolute;left:50%;top:4px;transform:translateX(-50%);font-size:6px}
  .envelope__url{position:absolute;left:0;right:0;bottom:6px;text-align:center;font-size:3px;color:var(--ink-soft)}

  /* business cards */
  .card{position:absolute;top:555px;width:87px;height:55px}
  .card--front{left:748px;background:var(--navy);display:flex;align-items:center;justify-content:center}
  .card--front .brand{font-size:6px}
  .card--back{left:871px;background:var(--paper)}
  .card__name{position:absolute;left:7px;top:8px;font-size:3.5px;font-weight:600;color:var(--navy);line-height:1.4}
  .card__name span{display:block;font-weight:400;color:var(--ink-soft)}
  .card--back .brand{position:absolute;right:8px;top:22px;font-size:5px}
  .card__contact{position:absolute;left:7px;top:33px;font-size:3px;line-height:1.5;color:var(--ink-soft)}
  .card__strip{position:absolute;left:0;right:0;bottom:4px;height:2px;background:var(--navy)}
</style>
</head>
<body>

<section class="folder" aria-label="Präsentationsmappe">
  <div class="folder__panel folder__panel--left">
    <div class="brand"><i class="mark"></i>HAUSLUMENA</div>
    <div class="pocket pocket--left"></div>
  </div>
  <div class="folder__panel folder__panel--right"></div>
  <article class="sheet sheet--in-folder">
    <div class="brand"><i class="mark"></i>HAUSLUMENA</div>
    <p class="sheet__sender"><b>HAUSLUMENA</b> · Parkallee 12 · 20144 Hamburg</p>
    <p class="sheet__address">Musterfirma<br>z. Hd. Herrn Mustermann<br>Musterstraße 1<br>12345 Musterstadt</p>
  </article>
  <div class="pocket pocket--right"></div>
</section>

<article class="sheet sheet--single" aria-label="Briefbogen">
  <div class="brand"><i class="mark"></i>HAUSLUMENA</div>
  <p class="sheet__sender"><b>HAUSLUMENA</b> · Parkallee 12 · 20144 Hamburg</p>
  <p class="sheet__address">Musterfirma<br>z. Hd. Herrn Mustermann<br>Musterstraße 1<br>12345 Musterstadt</p>
  <footer class="sheet__footer">
    <div>Geschäftsführer<br>Jonas Keller<br>Parkallee 12<br>20144 Hamburg</div>
    <div>Tel. 040 123456<br>Fax 040 123457<br>info@hauslumena.de<br>hauslumena.de</div>
    <div>Musterbank<br>IBAN DE00 0000 0000 0000<br>BIC MUSTDEXXXXX</div>
  </footer>
</article>

<article class="envelope" aria-label="Briefumschlag">
  <div class="envelope__flap"></div>
  <div class="brand brand--light">HAUSLUMENA</div>
  <p class="envelope__url">www.hauslumena.de</p>
</article>

<article class="card card--front" aria-label="Visitenkarte Vorderseite">
  <div class="brand brand--light"><i class="mark"></i>HAUSLUMENA</div>
</article>

<article class="card card--back" aria-label="Visitenkarte Rückseite">
  <p class="card__name">Jonas Keller<span>Sachverständiger</span></p>
  <div class="brand">HAUSLUMENA</div>
  <p class="card__contact">040 123456<br>info@hauslumena.de<br>hauslumena.de</p>
  <div class="card__strip"></div>
</article>

</body>
</html>
```